New business card for a regional office of a US M&A company

We need business card for a finance company, office based in Hong Kong , our Head office is in US, our business is to Merge and acquires companies , the new office will be a regional office for the Asia Pacific region. We want to use the head office logo as attached ( but don't have to be exactly the same, can be a variation to it) as a base and then add Asia Pacific alongside the logo.
We would prefer to have be bilingual Eng + Chinese, although we don't really have Chinese company name .

Industry/Entity Type

Business

Contact Information for Business Card

Clara Jo Tsang
 

VP,
APAC M&A Operations
Orin Vantage Asia Pacific Limited
 
Unit 1407, K18
18 Tai Lok Shan Road, 
Hong Kong 
 
M: +852 6038 1742
T : +852 2836 4100
F : +852 2836 4177
VOIP: 4158
 
cjtsang@orinvantage.com

Font styles to use
Serif
Sans Serif

Colors

Designer to choose colors to be used in the design.

Requirements
Must have
• APAC Office

```html
<!DOCTYPE html>
<html lang="en">
<head>
<meta charset="utf-8">
<title>Orin Vantage – Business Card</title>
<link rel="stylesheet" href="https://fonts.googleapis.com/css2?family=Open+Sans:wght@800&family=Roboto:wght@400&family=Roboto+Condensed:wght@700&display=swap">
<style>
  :root {
    --backdrop: #2a2b2d;
    --card-navy: #0f2942;
    --accent-cyan: #1fa9d3;
    --paper-white: #eef1f4;
    --text-light: #dfe5ea;
  }
  * { margin: 0; padding: 0; box-sizing: border-box; }
  html, body {
    width: 1200px;
    height: 960px;
    overflow: hidden;
    background: var(--backdrop);
  }
  .canvas {
    position: relative;
    width: 1200px;
    height: 960px;
  }
  .card {
    position: absolute;
    left: 320px;
    width: 600px;
    height: 342px;
    background: var(--card-navy);
    overflow: hidden;
  }
  /* Front face */
  .card-front { top: 110px; }
  .front-mark {
    position: absolute;
    left: 280px;
    top: 112px;
    width: 40px;
    height: 40px;
    background: var(--paper-white);
  }
  .front-name {
    position: absolute;
    left: 0;
    right: 0;
    top: 180px;
    text-align: center;
    font-family: "Open Sans", sans-serif;
    font-weight: 800;
    font-size: 50px;
    letter-spacing: -0.5px;
    color: var(--accent-cyan);
  }
  .front-web {
    position: absolute;
    left: 0;
    right: 0;
    top: 281px;
    text-align: center;
    font-family: "Roboto", sans-serif;
    font-size: 15px;
    letter-spacing: 6.5px;
    color: var(--text-light);
  }
  /* Back face */
  .card-back { top: 492px; }
  .holder-name {
    position: absolute;
    left: 34px;
    top: 26px;
    font-family: "Roboto Condensed", sans-serif;
    font-weight: 700;
    font-size: 21px;
    color: var(--accent-cyan);
  }
  .holder-title {
    position: absolute;
    left: 36px;
    top: 53px;
    font-family: "Roboto", sans-serif;
    font-size: 14px;
    color: var(--paper-white);
  }
  .contact-block {
    position: absolute;
    left: 35px;
    top: 127px;
    font-family: "Roboto", sans-serif;
    font-size: 14.5px;
    line-height: 18.5px;
    color: var(--text-light);
  }
  .address-lines { list-style: none; }
  .phone-lines { list-style: none; margin-top: 7px; }
  .phone-lines li { display: flex; align-items: center; gap: 8px; height: 19px; }
  .phone-lines svg { width: 15px; height: 15px; fill: var(--accent-cyan); flex: none; }
  .voip-line { margin-top: 11px; }
  .back-brand {
    position: absolute;
    left: 285px;
    top: 150px;
    width: 280px;
    text-align: center;
  }
  .back-brand-square {
    display: block;
    width: 44px;
    height: 44px;
    margin: 0 auto 14px;
    background: var(--paper-white);
  }
  .back-brand-name {
    font-family: "Open Sans", sans-serif;
    font-weight: 800;
    font-size: 32px;
    color: var(--paper-white);
  }
</style>
</head>
<body>
<main class="canvas">

  <section class="card card-front" aria-label="Card front">
    <span class="front-mark" aria-hidden="true"></span>
    <h1 class="front-name">ORIN VANTAGE</h1>
    <p class="front-web">www.orinvantage.com</p>
  </section>

  <section class="card card-back" aria-label="Card back">
    <h2 class="holder-name">CLARA JO TSANG</h2>
    <p class="holder-title">VP</p>

    <div class="contact-block">
      <ul class="address-lines">
        <li>APAC M&amp;A Operations</li>
        <li>Orin Vantage Asia Pacific Limited</li>
        <li>Unit 1407, K18</li>
        <li>18 Tai Lok Shan Road</li>
        <li>Hong Kong</li>
      </ul>
      <ul class="phone-lines">
        <li>
          <svg viewBox="0 0 16 16" aria-label="Telephone"><path d="M3.6 1.2 5.8 3.4c.4.4.4 1 0 1.4L4.7 5.9c.9 2 2.4 3.6 4.4 4.5l1.1-1.1c.4-.4 1-.4 1.4 0l2.2 2.2c.4.4.4 1 0 1.4l-1.2 1.2c-.7.7-1.8.9-2.7.5C6.2 13 3 9.8 1.4 6.1 1 5.2 1.2 4.1 1.9 3.4L3.1 1.2c.2-.2.4-.1.5 0Z"/></svg>
          +852 2836 4100
        </li>
        <li>
          <svg viewBox="0 0 16 16" aria-label="Mobile"><path d="M5 0.5h6c.8 0 1.4.6 1.4 1.4v12.2c0 .8-.6 1.4-1.4 1.4H5c-.8 0-1.4-.6-1.4-1.4V1.9C3.6 1.1 4.2.5 5 .5Zm.2 1.6v10.4h5.6V2.1H5.2Zm2.8 11.1a.7.7 0 1 0 0 1.4.7.7 0 0 0 0-1.4Z"/></svg>
          +852 6038 1742
        </li>
        <li>
          <svg viewBox="0 0 16 16" aria-label="Fax"><path d="M4 1h6l2 2v3H4V1Zm-2.5 6h13c.6 0 1 .4 1 1v5c0 .6-.4 1-1 1h-13c-.6 0-1-.4-1-1V8c0-.6.4-1 1-1Zm1.5 2v1.4h10V9H3Zm0 2.6V13h10v-1.4H3Z"/></svg>
          +852 2836 4177
        </li>
      </ul>
      <p class="voip-line">VOIP: 4158</p>
    </div>

    <div class="back-brand">
      <span class="back-brand-square" aria-hidden="true"></span>
      <p class="back-brand-name">ORIN VANTAGE</p>
    </div>
  </section>

</main>
</body>
</html>
```